Vellamoro Wine label**

Hi, we need a design for a white, red and sparkling wine label. We are a small italian restaurant (Vellamoro) and we want to release some wines under our personal brand. The restaurant has a rustic, italian provance style with with a slight modern, clean lines look. We would like a design that represent our mission to provide as authentic Italian food as we can, something that feels that it has been brought from the heart of Italy.
https://www.vellamorobistro.example/

```html
<!DOCTYPE html>
<html lang="it">
<head>
<meta charset="utf-8">
<title>Vellamoro Sangiovese – wine label</title>
<link rel="stylesheet" href="https://fonts.googleapis.com/css2?family=Raleway:wght@300&display=swap">
<style>
  :root {
    --backdrop: #8a8a8a;
    --paper: #fbfbf9;
    --ink: #121212;
    --gold-dark: #a8780c;
    --gold-mid: #c9971a;
    --gold-light: #ecd04a;
    --pattern-magenta: #d11479;
    --pattern-teal: #5fb3c4;
    --pattern-orange: #e0591f;
    --pattern-green: #1f9e4a;
    --pattern-plum: #3a0c2a;
    --pattern-lime: #d6d617;
  }
  * { margin: 0; padding: 0; box-sizing: border-box; }
  html, body {
    width: 750px;
    height: 1200px;
    overflow: hidden;
    background: var(--backdrop);
  }
  .canvas {
    position: relative;
    width: 750px;
    height: 1200px;
    background: linear-gradient(160deg, #9a9a9a 0%, #6e6e6e 100%);
  }
  .wine-label {
    position: absolute;
    left: 90px;
    top: 60px;
    width: 570px;
    height: 1080px;
    display: flex;
    box-shadow: 0 10px 30px rgba(0, 0, 0, 0.35);
  }
  .label-name-panel {
    width: 174px;
    height: 100%;
    background: var(--paper);
    display: flex;
    align-items: center;
    justify-content: center;
  }
  .brand-name {
    writing-mode: vertical-rl;
    transform: rotate(180deg);
    font-family: "Raleway", sans-serif;
    font-weight: 300;
    font-size: 112px;
    letter-spacing: 14px;
    color: var(--ink);
    line-height: 1;
  }
  .varietal-band {
    width: 59px;
    height: 100%;
    background: linear-gradient(180deg,
      var(--gold-dark) 0%,
      var(--gold-light) 10%,
      var(--gold-mid) 28%,
      var(--gold-dark) 55%,
      var(--gold-mid) 80%,
      var(--gold-light) 100%);
    display: flex;
    align-items: center;
    justify-content: center;
  }
  .varietal-name {
    writing-mode: vertical-rl;
    transform: rotate(180deg);
    font-family: "Raleway", sans-serif;
    font-weight: 300;
    font-size: 40px;
    letter-spacing: 24px;
    color: var(--ink);
    line-height: 1;
  }
  .pattern-field {
    flex: 1;
    height: 100%;
    background:
      linear-gradient(180deg,
        var(--pattern-orange) 0%,
        var(--pattern-magenta) 18%,
        var(--pattern-plum) 30%,
        var(--pattern-teal) 42%,
        var(--pattern-lime) 52%,
        var(--pattern-magenta) 62%,
        var(--pattern-green) 74%,
        var(--pattern-teal) 84%,
        var(--pattern-magenta) 92%,
        var(--pattern-orange) 100%);
  }
</style>
</head>
<body>
  <main class="canvas">
    <section class="wine-label">
      <div class="label-name-panel">
        <h1 class="brand-name">vellamoro</h1>
      </div>
      <div class="varietal-band">
        <p class="varietal-name">SANGIOVESE</p>
      </div>
      <div class="pattern-field" role="img" aria-label="Colourful geometric pattern of triangles and chevrons in magenta, teal, orange, green, lime and plum"></div>
    </section>
  </main>
</body>
</html>
```